Need help in designing new business card utilizing our new logo.

BuildMark Solutions works with Construction Business Owners, Managers & IT Professionals to strengthen software usage and increase user productivity.

Our Construction Accounting and Mobile Field Management Software Clients engage with us in the following areas:

New Software Implementations
Software Re-Implementations
Redesigning Software Usage at the User Level
Project Coordination & Management
Continued Software Support

Old tag line:
Weighing Options - Implementing Solutions

www.buildmark-solutions.example

Ridge 4 is a product, but not needed for a new business card.

```html
<!DOCTYPE html>
<html lang="en">
<head>
<meta charset="utf-8">
<title>BuildMark Solutions – Business Card</title>
<link rel="stylesheet" href="https://fonts.googleapis.com/css2?family=Roboto:wght@400;500;700&family=Roboto+Condensed:wght@700&display=swap">
<style>
  :root {
    --brand-blue: #0c1a9b;
    --brand-grey: #a6a7aa;
    --light-grey: #d3d4d6;
    --card-white: #f3f3f3;
    --text-dark: #333538;
    --backdrop: #b9b9b9;
  }
  * { box-sizing: border-box; margin: 0; padding: 0; }
  html, body { width: 1200px; height: 576px; overflow: hidden; }
  body {
    position: relative;
    background: var(--backdrop);
    font-family: "Roboto", Arial, sans-serif;
    color: var(--text-dark);
  }
  .card {
    position: absolute;
    top: 138px;
    background: var(--card-white);
    border-radius: 14px;
    overflow: hidden;
  }
  /* Front */
  .card-front { left: 82px; width: 485px; height: 294px; }
  .wordmark {
    display: flex; align-items: center; gap: 10px;
    font-family: "Roboto", Arial, sans-serif;
    font-weight: 700;
    color: var(--brand-blue);
    white-space: nowrap;
  }
  .wordmark-square { background: var(--brand-blue); flex: none; }
  .card-front .wordmark {
    position: absolute; top: 58px; left: 0; right: 0;
    justify-content: center; font-size: 27px;
  }
  .card-front .wordmark-square { width: 22px; height: 22px; }
  .services-band {
    position: absolute; left: 0; right: 0; top: 168px; height: 80px;
    background: var(--brand-blue);
    color: #fff;
    display: flex; flex-direction: column; justify-content: center; align-items: center;
    font-size: 13px; line-height: 18.5px; text-align: center;
  }
  .sep { margin: 0 9px; }
  .front-url {
    position: absolute; left: 0; right: 0; top: 262px;
    display: flex; justify-content: center; align-items: center; gap: 16px;
    font-size: 12px; color: var(--brand-blue);
  }
  .front-url .rule { width: 40px; height: 1px; background: var(--brand-grey); }
  /* Back */
  .card-back { left: 602px; width: 480px; height: 292px; }
  .edge-dot {
    position: absolute; left: -36px; top: 40px; width: 44px; height: 56px;
    border-radius: 50%; background: var(--brand-blue);
  }
  .holder { position: absolute; left: 24px; top: 44px; }
  .holder-name {
    font-family: "Roboto Condensed", "Arial Narrow", sans-serif;
    font-weight: 700; font-size: 21px; color: var(--brand-blue); line-height: 1.1;
  }
  .holder-title { font-size: 11px; margin-top: 3px; }
  .card-back .wordmark {
    position: absolute; right: 22px; top: 56px; font-size: 21px; gap: 8px;
  }
  .card-back .wordmark-square { width: 17px; height: 17px; }
  .contact-list {
    position: absolute; left: 30px; top: 134px; list-style: none;
    font-size: 11.5px; line-height: 16.5px;
  }
  .contact-list li { display: flex; align-items: center; gap: 8px; }
  .contact-list svg { width: 11px; height: 11px; fill: var(--brand-blue); flex: none; }
  .web-domain { color: var(--brand-blue); }
  .address {
    position: absolute; right: 22px; top: 135px;
    font-size: 11.5px; line-height: 16.5px; text-align: right; font-style: normal;
  }
  .wave { position: absolute; left: 0; bottom: 0; width: 480px; height: 110px; }
  .tagline {
    position: absolute; right: 36px; top: 238px; width: 140px;
    color: #fff; font-size: 11.5px; line-height: 19px; text-align: center;
  }
</style>
</head>
<body>

<section class="card card-front" aria-label="Card front">
  <div class="wordmark"><span class="wordmark-square"></span>BuildMark Solutions</div>
  <div class="services-band">
    <p>New Software Implementations<span class="sep">|</span>Software Re-Implementations</p>
    <p>Redesigning Software Usage at the User Level</p>
    <p>Project Coordination &amp; Management<span class="sep">|</span>Continued Software Support</p>
  </div>
  <div class="front-url"><span class="rule"></span>www.buildmark-solutions.example<span class="rule"></span></div>
</section>

<section class="card card-back" aria-label="Card back">
  <span class="edge-dot"></span>
  <div class="holder">
    <p class="holder-name">Dana R. Whitfield</p>
    <p class="holder-title">Owner</p>
  </div>
  <div class="wordmark"><span class="wordmark-square"></span>BuildMark Solutions</div>

  <ul class="contact-list">
    <li><svg viewBox="0 0 12 12" aria-hidden="true"><path d="M3 0h6a1 1 0 0 1 1 1v10a1 1 0 0 1-1 1H3a1 1 0 0 1-1-1V1a1 1 0 0 1 1-1zm0.5 1.5v7.5h5V1.5z"/></svg>555-014-2290</li>
    <li><svg viewBox="0 0 12 12" aria-hidden="true"><path d="M1 4c0-2 10-2 10 0v1H8.5V3.8h-5V5H1zM3 6h6l2 5H1z"/></svg>800-555-0137 ext. 100</li>
    <li><svg viewBox="0 0 12 12" aria-hidden="true"><path d="M0 2h12v1L6 7 0 3zM0 4.5l6 4 6-4V10H0z"/></svg>dana.whitfield@buildmark-solutions.example</li>
    <li><svg viewBox="0 0 12 12" aria-hidden="true"><path d="M6 0a6 6 0 1 0 0 12A6 6 0 0 0 6 0zm0 1c.8 0 1.6 1.8 1.8 4.5H4.2C4.4 2.8 5.2 1 6 1zM1 6.5h2.2c.1 1.7.4 3.1 1 4A5 5 0 0 1 1 6.5zm0-1A5 5 0 0 1 4.2 1.5c-.6.9-.9 2.3-1 4zm3.2 1h3.6C7.6 9.2 6.8 11 6 11S4.4 9.2 4.2 6.5zm4.6 0H11a5 5 0 0 1-3.2 4c.6-.9.9-2.3 1-4zm0-1c-.1-1.7-.4-3.1-1-4A5 5 0 0 1 11 5.5z"/></svg>www.<span class="web-domain">buildmark-solutions</span>.example</li>
  </ul>

  <address class="address">14B Harbor Lane - Suite 310<br>Millbrook Falls, NY 12000</address>

  <svg class="wave" viewBox="0 0 480 110" preserveAspectRatio="none" aria-hidden="true">
    <path d="M0 20 C80 60 200 75 300 45 C370 22 430 10 480 22 V32 C420 22 360 40 300 60 C200 90 90 80 0 38 Z" fill="var(--light-grey)"/>
    <path d="M0 40 C90 90 200 95 300 68 C370 48 430 28 480 30 V36 C430 36 370 58 300 80 C200 108 90 100 0 55 Z" fill="var(--brand-grey)"/>
    <path d="M0 62 C80 105 220 108 320 70 C390 42 440 32 480 35 V110 H0 Z" fill="var(--brand-blue)"/>
  </svg>
  <p class="tagline">Weighing Options<br>Implementing Solutions</p>
</section>

</body>
</html>
```